Flyer-Design für FUNKENHAUS
Zielgruppe
FUNKENHAUS kümmert sich dauerhaft um die Strom- und Gasverträge seiner privaten und gewerblichen Kunden. Konkret heißt das: Wir recherchieren jedes Jahr für den Kunden den günstigsten seriösen Strom/Gaslieferanten und wechseln den Kunden zu diesem Lieferanten. Wir übernehmen dabei sämliche Kommunikation mit Kunden, Lieferanten, Netzbetreibern etc. Der Kunde hat dauerhaft uns als Ansprechparter. Die Dienstleistung ist vergleichbar zu einem Steuerberater: Der Kunde bezahlt uns, damit wir uns um seine Verträge kümmern und für ihn sparen. Die Bezahlung erfolgt auf Provisionsbasis. 30% der durch einen Lieferantenwechsel eingesparten Kosten erhalten wir als Lohn. Das heißt für den Kunden: FUNKENHAUS hat dasselbe Ziel: Möglichst viel sparen, da dann auch das Kuchenstück (die 30%) für FUNKENHAUS größer ist. Außerdem hat der Kunde kein Risiko, denn wenn FUNKENHAUS nichts für ihn sparen kann, zahlt er auch nichts.
Die Zielgruppe des anzufertigenden Flyers sind Eigenheimbesitzer mit einer Gasheizung, d.h. eher ältere Menschen
Aufgabenstellung
Der Flyer (DIN A4) soll eine integrierte Antwortpostkarte enthalten, die ausgefüllt und ausgeschnitten an uns zurückgeschickt werden kann. Über die Postkarte kann dann bei uns ein Angebot angefordert werden.
Auf der Postkarte müssen damit für Strom und/oder Gas verschiedene Felder zur Verfügung stehen (Absendeadresse des Interessenten, Jahresverbrauch, derzeitige Preise, Kontaktmöglichkeiten & Sonderwünsche, etc.).
Da der Flyer über Briefmobil verteilt werden soll, wird auf den Flyer die Kundenadresse aufgedruckt ('An die Bewohner des Hauses....'. Dazu muss ein Feld freigehalten werden. Konkret muss das Layout entsprechend den Vorgaben der Post erstellt werden. Diese sind in einer angehängten .pdf zu finden auf Seite 37 der pdf (bzw. 35 des Dokuments)
Wegen Nachfrage: Der Flyer soll nicht gefaltet werden, er wird tatsächlich als nicht-umhüllte DIN-A4 Karte von der Post verteilt. Dazu muss die Empfängeradresse der Antwortpostkarte (d.h. Adresse von Funkenhaus) auf der Rückseite des Flyer angebracht werden.
Der Flyer soll unserem Corporate Design entsprechen, einiges an Material wird bereit gestellt
Das beigefügte Material muss nicht übernommen werden. Im Gegenteil wünschen wir gerne auch andere Vorschläge!

```html
<!DOCTYPE html>
<html lang="de">
<head>
<meta charset="utf-8">
<title>FUNKENHAUS – Flyer</title>
<link href="https://fonts.googleapis.com/css2?family=Montserrat:wght@300;400;500;600;700&family=Bangers&display=swap" rel="stylesheet">
<style>
  :root {
    --blue: #06569a;
    --ink: #0d4f8c;
    --orange: #ee7c00;
    --white: #ffffff;
    --hair: #5a1d10;
    --shirt: #f7d500;
  }
  * { margin: 0; padding: 0; box-sizing: border-box; }
  html, body { width: 849px; height: 1200px; overflow: hidden; background: var(--white); }
  .flyer {
    position: relative; width: 849px; height: 1200px; overflow: hidden;
    font-family: "Montserrat", Arial, sans-serif; color: var(--ink); background: var(--white);
  }
  .backdrop { position: absolute; inset: 0; }
  .brand {
    position: absolute; right: 31px; top: 104px;
    display: flex; align-items: center; gap: 14px;
  }
  .brand-dot { width: 30px; height: 30px; border-radius: 50%; background: var(--orange); }
  .brand-name { font-size: 46px; font-weight: 500; color: var(--ink); letter-spacing: 0.5px; line-height: 1; }
  .mailing-line {
    position: absolute; left: 45px; top: 203px;
    font-size: 12.5px; font-weight: 500; letter-spacing: 0.2px;
  }
  .intro {
    position: absolute; left: 38px; top: 268px;
    font-size: 18.3px; line-height: 24.25px; font-weight: 400; letter-spacing: 0.2px;
  }
  .portrait {
    position: absolute; left: 557px; top: 170px; width: 270px; height: 630px;
    border-radius: 130px 130px 0 0;
    background: linear-gradient(180deg, var(--hair) 0%, #e9a37a 38%, var(--shirt) 48%, #c8a800 100%);
  }
  .quote {
    position: absolute; left: 282px; top: 401px; width: 276px; height: 276px;
    display: flex; align-items: center; justify-content: center; text-align: center;
    font-family: "Bangers", "Comic Sans MS", cursive; color: var(--white);
    font-size: 34px; line-height: 33px; letter-spacing: 1px;
  }
  .how-title {
    position: absolute; left: 28px; top: 858px;
    font-size: 34px; font-weight: 400; color: var(--white); letter-spacing: 0.5px;
  }
  .step-num {
    position: absolute; font-size: 40px; font-weight: 300; color: var(--white); line-height: 1;
  }
  .step-title {
    position: absolute; font-size: 15.5px; font-weight: 600; color: var(--white);
    text-align: center; white-space: nowrap; letter-spacing: 0.3px;
  }
  .step-text {
    position: absolute; font-size: 9.3px; line-height: 11.6px; color: var(--white);
    text-align: center; font-weight: 400;
  }
  .step-text b { font-weight: 700; }
  .loop-label {
    position: absolute; left: 519px; top: 985px; width: 120px;
    font-size: 15px; font-weight: 600; color: var(--white); text-align: center; line-height: 17px;
  }
</style>
</head>
<body>
<div class="flyer">

  <svg class="backdrop" width="849" height="1200" viewBox="0 0 849 1200">
    <defs>
      <linearGradient id="arrowFadeRight" x1="0" x2="1">
        <stop offset="0" stop-color="#fff" stop-opacity="0"/>
        <stop offset="0.4" stop-color="#fff"/>
      </linearGradient>
      <linearGradient id="arrowFadeLeft" x1="1" x2="0">
        <stop offset="0" stop-color="#fff" stop-opacity="0"/>
        <stop offset="0.4" stop-color="#fff"/>
      </linearGradient>
    </defs>
    <!-- blue field with orange arc -->
    <path d="M255 800 C255 520 520 260 849 215 L849 1200 L0 1200 L0 800 Z" fill="var(--blue)"/>
    <path d="M255 800 C255 520 520 260 849 215" fill="none" stroke="var(--orange)" stroke-width="11"/>
    <line x1="0" y1="800" x2="258" y2="800" stroke="var(--orange)" stroke-width="11"/>
    <!-- cut line -->
    <line x1="258" y1="800" x2="849" y2="800" stroke="#fff" stroke-width="1.4" stroke-dasharray="6 5"/>
    <g fill="none" stroke="var(--orange)" stroke-width="3">
      <circle cx="11" cy="791" r="4.5"/>
      <circle cx="11" cy="809" r="4.5"/>
      <path d="M15 794 L44 809 M15 806 L44 791"/>
    </g>

    <!-- speech bubble -->
    <circle cx="420" cy="539" r="138" fill="var(--orange)"/>
    <path d="M400 410 C440 380 475 372 513 378 C480 388 462 405 445 418 Z" fill="var(--orange)"/>

    <!-- process arrows -->
    <g stroke-width="4" fill="none" stroke-linecap="round" stroke-linejoin="round">
      <line x1="205" y1="1047" x2="318" y2="1047" stroke="url(#arrowFadeRight)"/>
      <path d="M307 1037 L319 1047 L307 1057" stroke="#fff"/>
      <line x1="614" y1="1047" x2="470" y2="1047" stroke="url(#arrowFadeLeft)"/>
      <path d="M481 1037 L469 1047 L481 1057" stroke="#fff"/>
      <line x1="520" y1="928" x2="445" y2="1006" stroke="#fff"/>
      <path d="M444 992 L443 1008 L458 1007" stroke="#fff"/>
      <line x1="611" y1="928" x2="686" y2="1006" stroke="#fff"/>
      <path d="M673 1007 L688 1008 L687 992" stroke="#fff"/>
    </g>

    <!-- step 1: pointer -->
    <circle cx="143" cy="1047" r="45" fill="var(--orange)"/>
    <g fill="#fff">
      <circle cx="140" cy="1023" r="11" fill="none" stroke="#fff" stroke-width="4"/>
      <rect x="134" y="1020" width="11" height="40" rx="5.5"/>
      <rect x="124" y="1040" width="40" height="32" rx="9"/>
    </g>
    <!-- step 2: scales -->
    <circle cx="409" cy="1047" r="45" fill="var(--orange)"/>
    <g stroke="#fff" stroke-width="3.5" fill="none" stroke-linejoin="round">
      <line x1="409" y1="1018" x2="409" y2="1070"/>
      <line x1="380" y1="1025" x2="438" y2="1025"/>
      <path d="M383 1027 L372 1052 L394 1052 Z"/>
      <path d="M435 1027 L424 1052 L446 1052 Z"/>
      <line x1="394" y1="1071" x2="424" y2="1071"/>
    </g>
    <circle cx="409" cy="1018" r="4" fill="#fff"/>
    <!-- step 3: savings -->
    <circle cx="565" cy="888" r="45" fill="var(--orange)"/>
    <g fill="#fff">
      <ellipse cx="560" cy="896" rx="30" ry="20"/>
      <circle cx="575" cy="872" r="10"/>
      <rect x="540" y="906" width="9" height="14" rx="3"/>
      <rect x="568" y="906" width="9" height="14" rx="3"/>
    </g>
    <!-- step 4: refresh -->
    <circle cx="720" cy="1047" r="45" fill="var(--orange)"/>
    <g fill="none" stroke="#fff" stroke-width="7">
      <path d="M698 1040 A23 23 0 0 1 738 1032"/>
      <path d="M742 1054 A23 23 0 0 1 702 1062"/>
    </g>
    <path d="M731 1023 L748 1027 L740 1042 Z M709 1071 L692 1067 L700 1052 Z" fill="#fff"/>
  </svg>

  <div class="brand">
    <span class="brand-dot"></span>
    <span class="brand-name">FUNKENHAUS</span>
  </div>

  <p class="mailing-line">AN DIE BEWOHNER DES HAUSES</p>

  <p class="intro">FUNKENHAUS recherchiert jedes Jahr für<br>den Kunden den günstigsten seriösen Strom/<br>Gaslieferanten und wechselt den Kunden<br>zu diesem Lieferanten. Wir übernehmen<br>dabei sämliche Kommunikation mit<br>Kunden, Lieferanten, Netzbetrei-<br>bern etc. Sie haben dauerhaft<br>uns als Ansprechparter.<br>Die Dienstleistung ist ver-<br>gleichbar zu einem Steu-<br>erberater: Der Kunde be-<br>zahlt uns, damit wir uns<br>um seine Verträge küm-<br>mern und für ihn sparen.<br>Sie haben kein Risiko,<br>denn wenn FUNKEN-<br>HAUS nichts für Sie<br>sparen kann, zahlen<br>Sie auch nichts!</p>

  <div class="portrait" role="img" aria-label="Gezeichnete Frau mit Brille und gelbem Oberteil, die freundlich lächelt"></div>

  <p class="quote">MIT<br>FUNKEN-<br>HAUS SPAR'<br>ICH<br>180 EURO IM<br>JAHR!</p>

  <h2 class="how-title">SO EINFACH GEHT'S:</h2>

  <span class="step-num" style="left:74px;top:1028px;">1</span>
  <span class="step-num" style="left:334px;top:1028px;">2</span>
  <span class="step-num" style="left:490px;top:869px;">3</span>
  <span class="step-num" style="left:642px;top:1028px;">4</span>

  <p class="loop-label">DAUERHAFT<br>SPAREN</p>

  <h3 class="step-title" style="left:143px;top:1100px;transform:translateX(-50%);">TARIF-CHECK ANFORDERN</h3>
  <p class="step-text" style="left:23px;top:1121px;width:240px;">Fordern Sie <b>kostenlos und unverbindlich</b> ein angebot für die senkung ihrer<br>strom- und /oder Gaskosten</p>

  <h3 class="step-title" style="left:413px;top:1100px;transform:translateX(-50%);">BEST-TARIF CHECK</h3>
  <p class="step-text" style="left:303px;top:1121px;width:220px;">Wir prüfen objektiv <b>alle seriösen Anbieter</b> Ihrer Region und ermitteln den für Sie günstigsten Strom- und/oder Gas-Tarif</p>

  <h3 class="step-title" style="left:720px;top:1100px;transform:translateX(-50%);">BEST-CHECK AUTOMATIK</h3>
  <p class="step-text" style="left:603px;top:1121px;width:236px;">Wir behalten Ihre Tarife im Blick und sorgen dafür, dass Sie Strom und/or Gas <b>daurhaft vom günstigsten seriösen Anbieter</b> beziehen.</p>

  <h3 class="step-title" style="left:713px;top:827px;transform:translateX(-50%);">BEST-TARIFWECHSEL</h3>
  <p class="step-text" style="left:618px;top:849px;width:190px;">Wenn Sie einverstanden sind, überneh-men wür für Sie den sicheren Wechsel zum günstigsten seriösen Anbieter von Gas und/oder Strom. Unsere Vergütung beträgt <b>30 % der Kostenersparnis</b>.</p>

</div>
</body>
</html>
```